Transport & Storage Company needs a revamp of current card

Would like to keep same colours & basic design but would like to "sharpen" up look of card.

Please remove "The Brisk Haulers"

Please add 1800 418 239 on front & back of card

Please add email address on back of card - colin@bluegatefreight.com.au

I would like our ABN No - 38 214 906 731 on back of card (which currently has logo only). Logo on back of card can be removed if insufficient space.

Please design another card (same as above) but with Maren Ashcombe - 0431 702 548, maren@bluegatefreight.com.au

I do not want cards to look "too busy" so please re-arrange layout of card if necessary.

Target Market(s)

Transport & Storage

Industry/Entity Type

It Company

Contact Information for Business Card

Please refer to attached current business card

Font styles to use
Other font styles liked:
• Tahoma

Requirements
Must have
• Refer to project decsription
Nice to have
Should not have

```html
<!DOCTYPE html>
<html lang="en">
<head>
<meta charset="utf-8">
<title>Bluegate Freight – Business Card</title>
<link href="https://fonts.googleapis.com/css2?family=Source+Sans+3:wght@400;600;700&display=swap" rel="stylesheet">
<style>
  :root {
    --backdrop: #aeab87;
    --card: #ffffff;
    --purple: #743a83;
    --charcoal: #58585a;
    --ink: #1a1a1a;
    --font: "Source Sans 3", sans-serif;
  }
  html, body {
    margin: 0;
    padding: 0;
    width: 1083px;
    height: 1200px;
    overflow: hidden;
    background: var(--backdrop);
    font-family: var(--font);
  }
  .card {
    position: absolute;
    left: 76px;
    width: 929px;
    height: 543px;
    background: var(--card);
    box-shadow: 0 4px 14px rgba(0, 0, 0, 0.35);
    overflow: hidden;
  }
  .card--front { top: 47px; }
  .card--back { top: 623px; height: 541px; }
  .stripes {
    position: absolute;
    inset: 0;
    width: 100%;
    height: 100%;
  }
  .stripe--purple { fill: var(--purple); }
  .stripe--charcoal { fill: var(--charcoal); }
  .line {
    position: absolute;
    margin: 0;
    line-height: 1;
    white-space: nowrap;
  }
  .brand {
    display: flex;
    align-items: center;
    gap: 12px;
    font-weight: 700;
    color: var(--purple);
  }
  .brand__mark {
    width: 0.7em;
    height: 0.7em;
    background: var(--purple);
  }
  .card--front .brand {
    left: 48px;
    top: 96px;
    font-size: 54px;
  }
  .holder {
    left: 0;
    right: 0;
    top: 252px;
    text-align: center;
    padding-left: 175px;
    font-size: 39px;
    font-weight: 700;
    color: var(--purple);
  }
  .contact-right {
    right: 45px;
    text-align: right;
    font-size: 30px;
    color: var(--ink);
    letter-spacing: 0.04em;
  }
  .phone-mobile { top: 336px; }
  .phone-free { top: 375px; }
  .website {
    top: 424px;
    color: var(--purple);
    letter-spacing: 0.02em;
  }
  .centered {
    left: 0;
    right: 0;
    text-align: center;
    color: var(--purple);
  }
  .card--back .brand {
    left: 0;
    right: 0;
    justify-content: center;
    top: 195px;
    font-size: 60px;
  }
  .abn { top: 314px; font-size: 21px; }
  .back-phone { top: 364px; font-size: 35px; }
  .back-email { top: 413px; font-size: 35px; }
</style>
</head>
<body>

<section class="card card--front">
  <svg class="stripes" viewBox="0 0 1084 633" preserveAspectRatio="none" aria-hidden="true">
    <polygon class="stripe--charcoal" points="351,0 1084,0 1084,100"/>
    <polygon class="stripe--charcoal" points="0,470 1084,632 1084,633 930,633 0,542"/>
    <polygon class="stripe--purple" points="0,563 840,633 0,633"/>
  </svg>
  <div class="line brand"><span class="brand__mark"></span>Bluegate Freight</div>
  <p class="line holder">Colin Pratley</p>
  <p class="line contact-right phone-mobile">0412 583 602</p>
  <p class="line contact-right phone-free">1800 418 239</p>
  <p class="line contact-right website">www.bluegatefreight.com.au</p>
</section>

<section class="card card--back">
  <svg class="stripes" viewBox="0 0 1081 631" preserveAspectRatio="none" aria-hidden="true">
    <polygon class="stripe--purple" points="250,0 1081,0 1081,70"/>
    <polygon class="stripe--charcoal" points="0,0 110,0 1081,88 1081,163"/>
  </svg>
  <div class="line brand"><span class="brand__mark"></span>Bluegate Freight</div>
  <p class="line centered abn">ABN No - 38 214 906 731</p>
  <p class="line centered back-phone">1800 418 239</p>
  <p class="line centered back-email">colin@bluegatefreight.com.au</p>
</section>

</body>
</html>
```